Business Card Design

Electronic Security Installation Specialists

Check out our website at www.tallbrookllc.com to see what we do.

Industry/Entity Type

Business

Contact Information for Business Card

Tall Brook
Marjorie Hadley
281 Orchard Rise
Mapleton, WV 25871

Colors
3176b5
0455a3
ffffff

```html
<!DOCTYPE html>
<html lang="en">
<head>
<meta charset="utf-8">
<title>Tall Brook Business Card</title>
<link rel="stylesheet" href="https://fonts.googleapis.com/css2?family=Open+Sans:wght@400;600;700&display=swap">
<style>
  :root {
    --brand-blue: #0455a3;
    --brand-blue-light: #3176b5;
    --brand-blue-deep: #1f3f8a;
    --card-white: #ffffff;
    --card-grey: #ececec;
    --stripe-grey: #7a7a7a;
    --page-bg: #e9e7e4;
  }
  html, body {
    margin: 0;
    width: 1200px;
    height: 900px;
    overflow: hidden;
    background: var(--page-bg);
    font-family: "Open Sans", Arial, sans-serif;
  }
  .card {
    position: absolute;
    left: 110px;
    top: 170px;
    width: 980px;
    height: 560px;
    background: linear-gradient(135deg, var(--card-white), var(--card-grey));
    box-shadow: 0 12px 30px rgba(0,0,0,0.18);
    overflow: hidden;
  }
  .card-shapes {
    position: absolute;
    inset: 0;
  }
  .identity {
    position: absolute;
    left: 56px;
    top: 58px;
    color: var(--card-white);
  }
  .identity-name {
    margin: 0;
    font-size: 34px;
    font-weight: 700;
    line-height: 1.1;
  }
  .identity-title {
    margin: 4px 0 0;
    font-size: 26px;
    font-weight: 400;
  }
  .contact-list {
    position: absolute;
    left: 56px;
    bottom: 40px;
    margin: 0;
    padding: 0;
    list-style: none;
    color: var(--card-white);
    font-size: 19px;
    line-height: 1.35;
  }
  .contact-item {
    display: flex;
    align-items: flex-start;
    gap: 12px;
  }
  .contact-icon {
    flex: none;
    width: 18px;
    height: 18px;
    margin-top: 4px;
  }
  .brand-mark {
    position: absolute;
    right: 80px;
    top: 120px;
    width: 200px;
    height: 200px;
    border-radius: 50%;
    background: var(--brand-blue-deep);
    display: flex;
    align-items: center;
    justify-content: center;
  }
  .brand-name {
    color: var(--card-white);
    font-size: 32px;
    font-weight: 600;
  }
</style>
</head>
<body>
<div class="card">
  <svg class="card-shapes" width="980" height="560" viewBox="0 0 980 560" aria-hidden="true">
    <defs>
      <radialGradient id="panelGlow" cx="0.42" cy="0.5" r="0.65">
        <stop offset="0" stop-color="var(--brand-blue-light)"/>
        <stop offset="1" stop-color="var(--brand-blue-deep)"/>
      </radialGradient>
    </defs>
    <path class="grey-stripe" d="M0,0 H556 C596,200 680,420 800,560 H0 Z" fill="var(--stripe-grey)"/>
    <path class="blue-panel" d="M0,0 H536 C576,200 656,420 772,560 H0 Z" fill="url(#panelGlow)"/>
  </svg>

  <div class="identity">
    <h1 class="identity-name">Marjorie Hadley</h1>
    <p class="identity-title">Owner / C.E.O</p>
  </div>

  <ul class="contact-list">
    <li class="contact-item">
      <svg class="contact-icon" viewBox="0 0 18 18"><circle cx="9" cy="9" r="9" fill="#fff"/><path d="M4 9.5 9 5l5 4.5h-1.5V13h-7V9.5Z" fill="var(--brand-blue)"/></svg>
      <span>281 Orchard Rise,<br>Mapleton, WV 25871</span>
    </li>
    <li class="contact-item">
      <svg class="contact-icon" viewBox="0 0 18 18"><circle cx="9" cy="9" r="9" fill="#fff"/><path d="M6 4.5h2l.8 2.5-1.2.9a6 6 0 0 0 2.5 2.5l.9-1.2 2.5.8v2c0 .6-.5 1-1 1A8 8 0 0 1 5 5.5c0-.5.4-1 1-1Z" fill="var(--brand-blue)"/></svg>
      <span>304-555-0142</span>
    </li>
    <li class="contact-item">
      <svg class="contact-icon" viewBox="0 0 18 18"><circle cx="9" cy="9" r="9" fill="#fff"/><rect x="6" y="4" width="6" height="10" rx="1" fill="var(--brand-blue)"/></svg>
      <span>304-555-0187</span>
    </li>
    <li class="contact-item">
      <svg class="contact-icon" viewBox="0 0 18 18"><circle cx="9" cy="9" r="9" fill="#fff"/><rect x="5" y="7" width="8" height="6" fill="var(--brand-blue)"/><rect x="6.5" y="4.5" width="5" height="2.5" fill="var(--brand-blue)"/></svg>
      <span>304-555-0163</span>
    </li>
    <li class="contact-item">
      <svg class="contact-icon" viewBox="0 0 18 18"><circle cx="9" cy="9" r="9" fill="#fff"/><rect x="4.5" y="5.5" width="9" height="7" fill="var(--brand-blue)"/><path d="m4.5 5.5 4.5 4 4.5-4" stroke="#fff" fill="none"/></svg>
      <span>hello@tallbrookllc.com</span>
    </li>
    <li class="contact-item">
      <svg class="contact-icon" viewBox="0 0 18 18"><circle cx="9" cy="9" r="9" fill="#fff"/><circle cx="9" cy="9" r="4.5" fill="none" stroke="var(--brand-blue)"/><path d="M4.5 9h9M9 4.5c-2 2.5-2 6.5 0 9M9 4.5c2 2.5 2 6.5 0 9" stroke="var(--brand-blue)" fill="none"/></svg>
      <span>www.tallbrookllc.com</span>
    </li>
  </ul>

  <div class="brand-mark">
    <span class="brand-name">Tall Brook</span>
  </div>
</div>
</body>
</html>
```